LinkedIn Banner Design for B2B Consulting Firm

Take the already developed logo (attached) and incorporate it into a creative banner design for placement on LinkedIn (the social media platform targeting business users). The banner will be used on the firm's company profile page on LinkedIn (not yet created).

```html
<!DOCTYPE html>
<html lang="en">
<head>
<meta charset="utf-8">
<title>Corporate Fractional Marketing Banner</title>
<link rel="stylesheet" href="https://fonts.googleapis.com/css2?family=Poppins:wght@400;500;700&display=swap">
<style>
  :root {
    --page-bg: #d8d8d8;
    --banner-bg: #efefed;
    --green-dark: #3f6a4b;
    --green-soft: #9fb5a3;
    --ink: #0c1d10;
    --white: #ffffff;
    --chevron-light: #c9cfca;
  }
  html, body {
    margin: 0;
    padding: 0;
    width: 1149px;
    height: 1200px;
    overflow: hidden;
    background: var(--page-bg);
    font-family: "Poppins", sans-serif;
  }
  .canvas {
    position: relative;
    width: 1149px;
    height: 1200px;
  }
  .banner {
    position: absolute;
    left: 49px;
    top: 511px;
    width: 1051px;
    height: 178px;
    background: radial-gradient(ellipse at 70% 40%, #f4f4f2 0%, var(--banner-bg) 60%, #e8e8e6 100%);
    box-shadow: 0 8px 14px rgba(0,0,0,0.28);
    overflow: hidden;
  }
  .banner-graphics {
    position: absolute;
    inset: 0;
  }
  .headline {
    position: absolute;
    right: 34px;
    top: 36px;
    text-align: right;
  }
  .headline-kicker {
    margin: 0;
    font-size: 26px;
    font-weight: 400;
    line-height: 1;
    color: var(--green-dark);
    letter-spacing: 0.5px;
  }
  .headline-main {
    margin: 5px 0 0;
    font-size: 38px;
    font-weight: 700;
    line-height: 1;
    color: var(--ink);
    letter-spacing: 0.3px;
  }
  .headline-tag {
    display: inline-block;
    box-sizing: border-box;
    height: 27px;
    margin-top: 8px;
    padding: 3px 12px 0 17px;
    background: var(--green-dark);
    color: var(--white);
    font-size: 18px;
    font-weight: 400;
    line-height: 1.2;
    letter-spacing: 7.2px;
  }
</style>
</head>
<body>
<main class="canvas">
  <section class="banner">
    <svg class="banner-graphics" width="1051" height="178" viewBox="0 0 1051 178">
      <defs>
        <linearGradient id="stripeFade" x1="0" y1="0" x2="1" y2="1">
          <stop offset="0" stop-color="#7f9a86" stop-opacity="0.55"/>
          <stop offset="1" stop-color="#7f9a86" stop-opacity="0"/>
        </linearGradient>
        <linearGradient id="portraitTone" x1="0" y1="0" x2="0" y2="1">
          <stop offset="0" stop-color="#3a3a3a"/>
          <stop offset="1" stop-color="#262626"/>
        </linearGradient>
      </defs>

      <polygon class="stripe-soft" points="270,0 300,0 150,178 120,178" fill="url(#stripeFade)"/>
      <polygon class="stripe-soft" points="310,0 330,0 190,178 170,178" fill="url(#stripeFade)" opacity="0.6"/>

      <polygon class="chevron-band" points="209,178 367,30 523,178 481,178 367,70 251,178" fill="var(--green-dark)"/>

      <rect class="portrait" x="281" y="0" width="192" height="178" fill="url(#portraitTone)" role="img" aria-label="Photo: businessman in a dark suit holding a glowing light bulb in his open hand"/>

      <g class="arrow-marks" fill="none" stroke="var(--chevron-light)" stroke-width="4">
        <polyline points="521,146 509,156 524,168"/>
        <polyline points="533,150 521,160 536,172"/>
        <polyline points="545,154 533,164 548,176"/>
        <polyline points="557,158 545,168 560,180"/>
      </g>
    </svg>

    <div class="headline">
      <p class="headline-kicker">BEST-IN-CLASS</p>
      <h1 class="headline-main">CORPORATE FRACTIONAL</h1>
      <span class="headline-tag">MARKETING SERVICES</span>
    </div>
  </section>
</main>
</body>
</html>
```